Powerpoint design template for LUMOTEX for new digital platform

We would like to use a PowerPoint template, we would like to create a new page, we would like to create a new digital platform LUMOTEX for schools and parents for the creation of playful communication and educational tools for children to enhance their positive development, amaze them learn in a playful way. This platform is going to be the most creative, stimulating and innovative classroom, easy to use and fast to implement. Scrapbooking, collages ... Magazine, newsletters Diplomla / awards Slideshows Facebook Calendars Organizers Greetings Games ... This powerpoint template will be used essential to We are looking for a professional design, positioning our brand in the children market with an adult hearing. so you will need to find a good deal. Primary target: nurseries & schools from 0 to 18 years old and universities (in 2nd phase) Secondary target: small & medium businesses Third target: general public, and TPE If it is a color scheme, then it is suggested that it be marketed in Europe (UK, Italy, Spain) and in a 2nd Stage USA and other countries. multiple options for front page, insidious pages (multiple styles with limited text and extended text) and final contact page We need something to read, we can not do it too much, but we can not do it. , and inside pages aligned to our logo

Target Market(s)

Target 1; Education with teacher Target 2; parents and grandparents

Industry/Entity Type

Education

Font styles to use
Other font styles liked:
• not decided. but not too fancy

Requirements
Must have
• Multi page options for front page, page insides (multiple styles with limited text and extended text) and final page contact
Nice to have
• do not have a lot of ideas. We need something to read, we can not get away from it
Should not have
• not too fancy and busy: keep clarity & simplicity while reassuring on quality

```html
<!DOCTYPE html>
<html lang="en">
<head>
<meta charset="utf-8">
<title>LUMOTEX – Project Slide</title>
<link href="https://fonts.googleapis.com/css2?family=Roboto+Condensed:wght@400;700&family=Mulish:wght@400;600&display=swap" rel="stylesheet">
<style>
  :root {
    --lime: #dbe241;
    --lime-light: #c6d83a;
    --lime-pale: #e8ee7a;
    --cream: #fdf7c0;
    --white: #ffffff;
    --orange: #f7941d;
    --ink: #2b2b2b;
    --body: #4a4a4a;
    --gold: #f7b92a;
    --pink: #e8326e;
    --teal: #4a8a90;
    --violet: #9a72b8;
  }
  * { margin: 0; padding: 0; box-sizing: border-box; }
  html, body { width: 1200px; height: 900px; overflow: hidden; background: var(--white); }
  .slide { position: relative; width: 1200px; height: 900px; overflow: hidden; background: var(--white); }
  .frame { position: absolute; inset: 0; }
  .content-panel { position: absolute; left: 0; top: 132px; width: 1200px; height: 690px; background: var(--cream); }
  .slide-title {
    position: absolute; left: 30px; top: 28px;
    font: 700 45px/1 "Roboto Condensed", sans-serif; color: var(--ink); letter-spacing: 0.3px;
  }
  .brand-name {
    position: absolute; left: 995px; top: 40px; width: 170px; text-align: center;
    font: 700 30px/1 "Roboto Condensed", sans-serif; color: var(--ink);
  }
  .topics { position: absolute; left: 52px; top: 236px; width: 1060px; list-style: none; }
  .topic { position: relative; padding-left: 100px; }
  .topic + .topic { margin-top: 28px; }
  .topic:nth-child(3) { margin-top: 20px; }
  .topic-icon { position: absolute; left: 2px; top: 12px; width: 56px; height: 66px; border-radius: 4px; transform: rotate(-14deg); }
  .topic-heading { font: 600 30px/1.2 "Mulish", sans-serif; }
  .topic-text { font: 400 25px/36px "Mulish", sans-serif; color: var(--body); }
  .topic--gold .topic-heading { color: var(--gold); }
  .topic--pink .topic-heading { color: var(--pink); }
  .topic--teal .topic-heading { color: var(--teal); }
  .topic--gold .topic-icon { background: var(--violet); }
  .topic--pink .topic-icon { background: var(--pink); }
  .topic--teal .topic-icon { background: var(--teal); }
  .site-link { position: absolute; left: 21px; top: 853px; font: 400 24px/1 "Roboto Condensed", sans-serif; color: var(--ink); }
  .page-number { position: absolute; left: 1078px; top: 855px; font: 400 22px/1 "Roboto Condensed", sans-serif; color: var(--ink); }
</style>
</head>
<body>
<main class="slide">
  <div class="content-panel"></div>

  <svg class="frame" width="1200" height="900" viewBox="0 0 1200 900" aria-hidden="true">
    <!-- header band -->
    <polygon points="0,0 958,0 918,110 0,110" fill="var(--lime)"/>
    <polygon points="940,0 970,0 930,110 905,110" fill="var(--lime-light)"/>
    <!-- brand plate -->
    <polygon points="992,14 1160,0 1182,84 1130,118 1000,96" fill="var(--lime)"/>
    <polygon points="1140,10 1188,22 1170,100 1130,118" fill="var(--lime-light)"/>
    <!-- footer band -->
    <polygon points="0,834 976,834 1030,900 0,900" fill="var(--lime)"/>
    <polygon points="976,834 1000,834 1052,900 1028,900" fill="var(--lime-light)"/>
    <polygon points="996,834 1200,834 1200,900 1052,900" fill="var(--orange)"/>
  </svg>

  <h1 class="slide-title">PROJECT TITLE HERE</h1>
  <div class="brand-name">LUMOTEX</div>

  <ul class="topics">
    <li class="topic topic--gold">
      <span class="topic-icon" role="img" aria-label="Purple book icon"></span>
      <h2 class="topic-heading">Subtext here</h2>
      <p class="topic-text">Lemon drops oat cake oat cake sugar plum sweet gingerbread chocolate cake gingerbread. Lemon drops oat cake oat cake sugar plum sweet</p>
    </li>
    <li class="topic topic--pink">
      <span class="topic-icon" role="img" aria-label="Pink book icon"></span>
      <h2 class="topic-heading">Subtext here</h2>
      <p class="topic-text">Lemon drops oat cake oat cake sugar plum sweet gingerbread chocolate cake gingerbread. Lemon drops oat cake oat cake sugar plum sweet</p>
    </li>
    <li class="topic topic--teal">
      <span class="topic-icon" role="img" aria-label="Teal book icon"></span>
      <h2 class="topic-heading">Subtext here</h2>
      <p class="topic-text">Lemon drops oat cake oat cake sugar plum sweet gingerbread chocolate cake gingerbread. Lemon drops oat cake oat cake sugar plum sweet</p>
    </li>
  </ul>

  <footer>
    <span class="site-link">www.lumotex.com</span>
    <span class="page-number">Page : 01</span>
  </footer>
</main>
</body>
</html>
```